Business Card Design Project

I need a business card designed from scratch. I have an existing logo that I can upload in Illustrator for modification or redesign.

The Company is called Query Lanterns http://querylanterns.com.au and we provide Search Engine Optimization services to Australian businesses. The current logo signifies an increase in visitors, profits etc...

There are no restrictions as to the redesign - colours, style etc are all open to change.

Cards will be full colour and one sided printed at http://www.cardmoxel.com.au so check their requirements for file format and sizes etc.

I will expect all original files upon completion of project.

Target Market(s)

Any business with a web site looking to improve their search engine rankings

Industry/Entity Type

Business

Requirements
Must have
• I like modern, sleek designs. Clean, not fussy, uncluttered.

```html
<!DOCTYPE html>
<html lang="en">
<head>
<meta charset="utf-8">
<title>Query Lanterns — Business Card</title>
<link rel="stylesheet" href="https://fonts.googleapis.com/css2?family=Source+Sans+3:wght@400;600;700&display=swap">
<style>
  :root {
    --backdrop: #efece6;
    --card-white: #ffffff;
    --panel-light: #2f6db3;
    --panel-dark: #173e78;
    --brand-blue: #1f6fb8;
    --brand-yellow: #f3c21c;
    --ink-light: #ffffff;
    --card-edge: #2a2a2a;
  }
  * { box-sizing: border-box; margin: 0; padding: 0; }
  html, body { width: 1200px; height: 686px; overflow: hidden; }
  body {
    background: var(--backdrop);
    font-family: "Source Sans 3", "Myriad Pro", sans-serif;
    position: relative;
  }
  .card {
    position: absolute;
    width: 494px;
    height: 281px;
    background: var(--card-white);
    border-radius: 18px;
    border-bottom: 1px solid var(--card-edge);
    border-right: 1px solid var(--card-edge);
    box-shadow: 2px 2px 4px rgba(0,0,0,.35);
    overflow: hidden;
  }
  .card--front { left: 81px; top: 139px; }
  .card--back  { left: 617px; top: 267px; }

  .front-panel { position: absolute; inset: 0; }

  .brand {
    position: absolute;
    display: flex;
    align-items: center;
    gap: 8px;
    color: var(--brand-blue);
    font-weight: 700;
    white-space: nowrap;
  }
  .brand__dot {
    border-radius: 50%;
    background: var(--brand-yellow);
    flex: none;
  }
  .brand--front { left: 14px; top: 124px; font-size: 25px; }
  .brand--front .brand__dot { width: 16px; height: 16px; }
  .brand--back { left: 0; right: 0; top: 118px; justify-content: center; font-size: 34px; }
  .brand--back .brand__dot { width: 22px; height: 22px; }

  .contact { position: absolute; color: var(--ink-light); white-space: nowrap; }
  .contact__name { left: 274px; top: 49px; font-size: 17px; font-weight: 600; }
  .contact__title { left: 270px; top: 77px; font-size: 12px; font-weight: 700; }
  .contact__line {
    font-size: 12.5px;
    display: flex; align-items: center; gap: 4px;
  }
  .contact__line svg { width: 11px; height: 11px; fill: var(--ink-light); flex: none; }
  .line-phone { left: 253px; top: 119px; }
  .line-mail  { left: 249px; top: 138px; }
  .line-web   { left: 246px; top: 158px; }
  .address { font-size: 12.5px; line-height: 17px; }
  .address--street { left: 243px; top: 193px; }
  .address--state  { left: 240px; top: 210px; }
</style>
</head>
<body>
  <section class="card card--front" aria-label="Card front">
    <svg class="front-panel" viewBox="0 0 494 281" width="494" height="281">
      <defs>
        <radialGradient id="panelGlow" cx="0.35" cy="0.3" r="0.9">
          <stop offset="0" stop-color="var(--panel-light)"/>
          <stop offset="1" stop-color="var(--panel-dark)"/>
        </radialGradient>
      </defs>
      <polygon points="276,0 494,0 494,281 204,281 262,23 248,26" fill="url(#panelGlow)"/>
    </svg>

    <div class="brand brand--front"><span class="brand__dot"></span>Query Lanterns</div>

    <p class="contact contact__name">Your Name</p>
    <p class="contact contact__title">Title</p>
    <p class="contact contact__line line-phone">
      <svg viewBox="0 0 24 24"><path d="M6.6 10.8a15 15 0 006.6 6.6l2.2-2.2c.3-.3.7-.4 1-.2 1.1.4 2.3.6 3.6.6.6 0 1 .4 1 1V20c0 .6-.4 1-1 1A17 17 0 013 4c0-.6.4-1 1-1h3.5c.6 0 1 .4 1 1 0 1.3.2 2.5.6 3.6.1.3 0 .7-.2 1z"/></svg>123-456-7890
    </p>
    <p class="contact contact__line line-mail">
      <svg viewBox="0 0 24 24"><path d="M2 5h20v14H2z M2 5l10 8 10-8" fill="var(--ink-light)" stroke="var(--panel-dark)" stroke-width="1.5"/></svg>inquiry@querylanterns.com.au.com
    </p>
    <p class="contact contact__line line-web">
      <svg viewBox="0 0 24 24"><circle cx="12" cy="12" r="10" fill="none" stroke="var(--ink-light)" stroke-width="2"/><path d="M2 12h20M12 2c3 3 3 17 0 20M12 2c-3 3-3 17 0 20" fill="none" stroke="var(--ink-light)" stroke-width="1.6"/></svg>www.querylanterns.com.au
    </p>
    <p class="contact address address--street">Street name City</p>
    <p class="contact address address--state">State, zip code</p>
  </section>

  <section class="card card--back" aria-label="Card back">
    <div class="brand brand--back"><span class="brand__dot"></span>Query Lanterns</div>
  </section>
</body>
</html>
```